Patent Law

Need to develop a home page for a patent lawyer.

Colors should go with logo, blues...

Company Name- Velun Tresk, PLLC

Company Overview-

I am an Intellectual Property Lawyer and focus on patents, copyrights, trademarks, & trade secrets. I work with small businesses and start ups in the chemical and biotech industries.

Why Us-

I am small firm that can provide large-firm service at a reasonable price. I also can charge flat-fees for entreprenuers in certain practice areas.

Services-
Intellectual Property
Patents
Copyrights
Trademarks
Trade secrets
Healthcare Compliance
Elder law
Wills
Trusts

Website we like-
http://www.quorvantlegal.example/ - within industry!!
http://www.daltrowemiko.example/
http://ulbrixtane.example/
http://thegravelcounsel.example/

Target Market(s)

My customers will be small business, specifically small start-up companies in the chemical and biotech arena.

Industry/Entity Type

Trade

Requirements
Must have
• Colors should go with logo, blues...

```html
<!DOCTYPE html>
<html lang="en">
<head>
<meta charset="utf-8">
<title>Velun Tresk, PLLC — Home</title>
<link href="https://fonts.googleapis.com/css2?family=Open+Sans:wght@400;600&family=Cinzel:wght@500&display=swap" rel="stylesheet">
<style>
:root{
  --blue:#2a7bc0;
  --blue-dark:#1f6aa8;
  --navy:#1c3f7a;
  --text:#555;
  --text-dark:#333;
  --panel:#f7f7f7;
  --border:#dcdcdc;
  --red:#e04b4b;
}
*{margin:0;padding:0;box-sizing:border-box}
html,body{width:1200px;height:1200px;overflow:hidden;background:#fff}
body{position:relative;font-family:'Open Sans',Arial,sans-serif;color:var(--text)}
.abs{position:absolute}
.header{position:absolute;left:0;top:0;width:1200px;height:136px;border-bottom:1px solid #e3e3e3;box-shadow:0 1px 3px rgba(0,0,0,.06)}
.brand{left:131px;top:100px;font-family:'Cinzel',serif;font-size:17px;letter-spacing:.5px;color:var(--text-dark);display:flex;align-items:center;gap:8px}
.brand-dot{width:12px;height:12px;border-radius:50%;background:var(--navy)}
.call{left:750px;top:16px;font-size:18px;color:#666}
.call span{color:var(--blue)}
.world{left:928px;top:20px;width:84px;height:42px;background:linear-gradient(#dcdcdc,#cfcfcf);border-radius:6px}
.search{left:1035px;top:21px;width:37px;height:26px;background:#e4e4e4;border-radius:2px}
.nav{left:433px;top:103px;font-size:15px;color:#777;display:flex;gap:0}
.nav a{color:#777;text-decoration:none}
.nav a.active{color:var(--blue)}
.nav .sep{margin:0 15px;color:#999}
.hero{left:0;top:137px;width:1200px;height:470px;background:linear-gradient(90deg,#b9bfc6 0%,#dfe2e5 30%,#cdd2d8 55%,#e6e8ea 80%,#c8ccd1 100%)}
.cap1{left:414px;top:430px;width:373px;height:55px;background:rgba(40,40,40,.88);color:#fff;font-size:31px;text-align:center;line-height:52px}
.cap2{left:357px;top:488px;width:487px;height:56px;background:rgba(40,40,40,.88);color:#1e9be0;font-size:34px;text-align:center;line-height:52px}
.dots{left:557px;top:571px;display:flex;gap:7px}
.dots i{width:16px;height:16px;border-radius:50%;background:#444;display:block}
.dots i.on{background:#1e9be0}
.panel{top:640px;height:409px;background:var(--panel);border:1px solid var(--border)}
.panel h2{position:absolute;left:21px;top:13px;font-size:26px;font-weight:400;color:var(--blue);letter-spacing:.3px}
.photo{left:21px;top:62px;width:257px;height:139px;background:linear-gradient(90deg,#e9ecef,#cfd3d8 50%,#e9ecef);border:1px solid #ddd}
.copy{left:21px;top:214px;width:260px;font-size:13px;line-height:23px;color:var(--text)}
.btn{left:21px;top:352px;width:127px;height:40px;background:linear-gradient(var(--blue),var(--blue-dark));color:#fff;font-size:14px;line-height:40px;text-align:center;border-radius:2px}
.services{left:21px;top:56px;width:255px;list-style:none}
.services li{height:31px;border-bottom:1px dashed #d3d3d3;font-size:13px;line-height:30px;padding-left:32px;position:relative;color:var(--text)}
.services li:last-child{border-bottom:none}
.services li::before{content:"";position:absolute;left:1px;top:10px;width:10px;height:10px;border-radius:50%;background:var(--red)}
.services li::after{content:"";position:absolute;left:4px;top:13px;width:3px;height:3px;border-right:1px solid #fff;border-top:1px solid #fff;transform:rotate(45deg)}
.map{left:21px;top:62px;width:257px;height:165px;background:linear-gradient(135deg,#efe9dd,#e4e0d4 60%,#b9d3f0);border:1px solid #ddd}
.contact{left:21px;top:245px;font-size:13px;color:var(--text);line-height:18px}
.contact .label{color:var(--text-dark);font-weight:600;font-size:14px}
.contact .firm{color:var(--blue);font-size:17px;margin-top:4px;line-height:24px}
.contact .row{display:flex;margin-top:6px}
.contact .row b{width:72px;font-weight:600;color:var(--text-dark)}
.contact .row span{color:var(--blue)}
.rule{left:130px;top:1070px;width:940px;height:3px;background:#e6e6e6}
.links{left:129px;top:1093px;font-size:13px;color:#666}
.links .sep{margin:0 9px;color:#aaa}
.social{left:931px;top:1097px;display:flex;gap:6px}
.social i{width:30px;height:30px;border-radius:3px;background:var(--blue);display:block}
.legal{left:131px;top:1132px;font-size:12px;color:#777;line-height:20px}
.legal span{color:var(--blue)}
</style>
</head>
<body>
<header class="header">
  <div class="abs brand"><span class="brand-dot"></span>VELUN TRESK, PLLC</div>
  <div class="abs call">Call: <span>041 728 5530</span></div>
  <div class="abs world" role="img" aria-label="Grey world map"></div>
  <div class="abs search">
    <svg width="37" height="26" viewBox="0 0 37 26"><circle cx="16" cy="11" r="4" fill="none" stroke="#2a7bc0" stroke-width="2"/><line x1="19" y1="14" x2="24" y2="18" stroke="#2a7bc0" stroke-width="2.5"/></svg>
  </div>
  <nav class="abs nav">
    <a class="active">Home</a><span class="sep">/</span>
    <a>Who We Are</a><span class="sep">/</span>
    <a>What We Do</a><span class="sep">/</span>
    <a>Media &amp; Events</a><span class="sep">/</span>
    <a>Careers</a><span class="sep">/</span>
    <a>Contact Us</a>
  </nav>
</header>

<section class="abs hero" role="img" aria-label="Photo of a smiling team of business professionals"></section>
<div class="abs cap1">Lorem ipsum dolor sit</div>
<div class="abs cap2">Consectetuer adipiscing elit</div>
<div class="abs dots"><i class="on"></i><i></i><i></i><i></i></div>

<section class="abs panel" style="left:130px;width:300px">
  <h2>WHY US</h2>
  <div class="abs photo" role="img" aria-label="Photo of a confident businesswoman with arms crossed"></div>
  <p class="abs copy">Aliquam molestie, mi et imperdiet euis-mod, dui purus auctor tellus, et interdum lacus lectus et ante. Sed accumsan sollicitudin sapien, sit amet adipiscing turpis gravida ac.</p>
  <div class="abs btn">LEARN MORE</div>
</section>

<section class="abs panel" style="left:450px;width:300px">
  <h2>WHAT WE DO</h2>
  <ul class="abs services">
    <li>Intellectual Property</li>
    <li>Patents</li>
    <li>Copyrights</li>
    <li>Trademarks</li>
    <li>Trade secrets</li>
    <li>Healthcare Compliance</li>
    <li>Elder law</li>
    <li>Wills</li>
    <li>Trusts</li>
  </ul>
  <div class="abs btn">LEARN MORE</div>
</section>

<section class="abs panel" style="left:771px;width:300px">
  <h2>CONTACT INFO</h2>
  <div class="abs map" role="img" aria-label="Street map with office location pins"></div>
  <div class="abs contact">
    <div class="label">Contact Address:</div>
    <div class="firm">Velun Tresk, PLLC</div>
    <div>4172 Harlow Lane</div>
    <div>Dunmere, K17 3PW</div>
    <div class="row"><b>Tel:</b><span>041 728 5530</span></div>
    <div class="row"><b>Email:</b><span>info@veluntresk.example</span></div>
  </div>
</section>

<footer>
  <div class="abs rule"></div>
  <div class="abs links">privacy policy<span class="sep">|</span>terms of use<span class="sep">|</span>site map</div>
  <div class="abs social"><i></i><i></i><i></i><i></i></div>
  <div class="abs legal">Copyright © 2014. <span>Velun Tresk, PLLC.</span><br>All Right Reserved</div>
</footer>
</body>
</html>
```